Career-focused learning application platform

We have a K-12 learning application platform designed for grades 6-12 that needs user interface improvements that provide a positive experience for all users (teachers and students). The learning platform provides career-focused math curriculum and career exploration resources. We would like to improve the user-interface with engaging design elements without taking away from the functionality and performance of the platform.

```html
<!DOCTYPE html>
<html lang="en">
<head>
<meta charset="utf-8">
<title>Trailmark Careers – Learning Platform Screens</title>
<link rel="stylesheet" href="https://fonts.googleapis.com/css2?family=Roboto:wght@400;500;700&display=swap">
<style>
:root{
  --orange:#f7941d;
  --orange-dark:#ef8a10;
  --sidebar-top:#5a5a5a;
  --slate:#5c5c5c;
  --ink:#222;
  --text:#555;
  --muted:#888;
  --line:#e2e2e2;
  --red:#e01b1b;
  --page:#ebebeb;
  --white:#fff;
}
*{box-sizing:border-box;margin:0;padding:0}
html,body{width:1200px;height:3647px;overflow:hidden}
body{background:var(--page);font-family:"Roboto",Arial,sans-serif;color:var(--text);position:relative}
.screen{position:absolute;left:59px;width:1082px;background:var(--white);overflow:hidden}
.screen-1{top:82px;height:1182px}
.screen-2{top:1316px;height:1182px}
.screen-3{top:2561px;height:1002px}
.sidebar{position:absolute;left:0;top:0;bottom:0;width:238px;background:var(--orange)}
.brand{height:112px;background:var(--sidebar-top);display:flex;align-items:center;justify-content:center;gap:8px}
.brand-mark{width:14px;height:14px;border-radius:50%;background:var(--white)}
.brand-name{color:var(--white);font-weight:700;font-size:15px;letter-spacing:.3px}
.nav{list-style:none;padding-top:28px}
.nav li{display:flex;align-items:center;gap:14px;height:38px;padding-left:42px;color:var(--white);font-size:11.5px;font-weight:700;letter-spacing:.2px}
.nav i{width:10px;height:10px;background:var(--white);border-radius:2px;display:block}
.topbar{position:absolute;left:238px;right:0;top:0;height:50px;display:flex;align-items:center;padding:0 46px;box-shadow:0 2px 6px rgba(0,0,0,.06);font-size:11.5px;color:#444}
.topbar .mail,.topbar .login{display:flex;align-items:center;gap:14px}
.topbar .login{margin-left:34px;font-weight:500}
.topbar .right{margin-left:auto;display:flex;align-items:center;gap:0}
.topbar .avatar{width:30px;height:30px;border-radius:50%;background:linear-gradient(#8a8a8a,#4a4a4a);margin-left:50px;margin-right:14px}
.user b{display:block;font-size:11.5px;color:#222}
.user span{font-size:11px;color:#666}
.ic{display:block}
.main{position:absolute;left:238px;right:0;top:50px;bottom:0}
.page-title{position:absolute;left:0;right:0;top:42px;text-align:center;color:var(--orange);font-size:25px;font-weight:700;letter-spacing:.3px}
.back{position:absolute;left:46px;top:48px}
.h-section{color:var(--orange);font-size:26px;font-weight:700;position:absolute}
.btn{display:inline-flex;align-items:center;gap:8px;font-weight:700;font-size:11px;color:var(--white);border-radius:2px;white-space:nowrap}
.btn .dot{width:9px;height:9px;border-radius:50%;background:var(--white);display:block}
.btn-dark{background:var(--slate)}
.btn-orange{background:var(--orange)}
/* screen 1 */
.spotlight{position:absolute;left:49px;top:131px;width:350px}
.job-title{color:var(--orange);font-size:16px;font-weight:500}
.label{font-size:11px;font-weight:700;color:#222;margin-top:18px}
.spotlight p{font-size:11.5px;line-height:19px;text-align:justify;margin-top:10px}
.earnings{display:flex;margin-top:14px;font-size:11.5px}
.earnings div{padding-right:18px;margin-right:18px;border-right:1px solid var(--line)}
.earnings div:last-child{border:0}
.earnings b{display:block;color:var(--orange);font-weight:500;margin-top:3px}
.spotlight .btn{margin-top:26px;padding:0 16px;height:40px;font-size:12px}
.media{position:absolute;left:452px;top:108px;width:361px;height:304px;padding:6px;background:var(--white);box-shadow:0 2px 8px rgba(0,0,0,.18)}
.media .photo{width:100%;height:100%;background:linear-gradient(135deg,#d9dde2,#9aa4ae 55%,#50627a);position:relative}
.play{position:absolute;left:50%;top:50%;width:30px;height:30px;margin:-15px;border-radius:50%;background:var(--orange)}
.view-all{position:absolute;right:40px;top:490px;color:var(--orange);font-size:11px;font-weight:700;text-decoration:underline;display:flex;gap:8px;align-items:center}
.class-card{position:absolute;top:544px;width:357px;height:161px;background:var(--white);box-shadow:0 2px 10px rgba(0,0,0,.12);padding:26px 28px}
.class-card .who{display:flex;align-items:center;gap:10px;font-size:11.5px;font-weight:700;color:#222}
.class-card .period{font-size:12.5px;font-weight:500;color:#333;margin-top:12px}
.class-card .sub{font-size:11.5px;margin-top:8px}
.class-card .btn{margin-top:14px;height:32px;padding:0 11px;font-size:10px}
.cover{position:absolute;background:linear-gradient(160deg,#28527a 0 38%,var(--orange) 38%);border-radius:3px}
.class-card .cover{right:28px;top:36px;width:88px;height:90px}
.lessons-intro{position:absolute;left:49px;top:818px;font-size:13.5px;color:#444}
.table{position:absolute;left:49px;top:857px;width:757px;border-collapse:collapse;font-size:11.5px;text-align:center}
.table th{background:var(--slate);color:var(--white);height:43px;font-weight:500;font-size:13px;border-right:2px solid var(--white)}
.table th:last-child{border-right:0}
.table td{height:42.5px;border:1px solid var(--line);color:#666}
.table td.due{color:var(--red);font-weight:500}
/* screen 2 */
.teacher-row{position:absolute;left:64px;top:100px;right:64px;display:flex;align-items:center;font-size:12px}
.teacher-row .who{display:flex;align-items:center;gap:10px;font-weight:700;color:#222}
.teacher-row .period{margin-left:22px;font-weight:500;color:#333}
.teacher-row .sub{margin-left:22px;font-size:11px;color:#777}
.teacher-row .btn{height:30px;padding:0 13px;font-size:9.5px}
.teacher-row .btn-orange{margin-left:auto}
.teacher-row .btn-dark{margin-left:14px}
.tabs{position:absolute;display:flex;font-size:11.5px;font-weight:700;color:#222}
.tabs .tab{display:flex;align-items:center;gap:8px;padding-bottom:8px}
.tabs .active{color:var(--orange);border-bottom:2px solid var(--orange)}
.lesson-tabs{left:0;right:0;justify-content:center;gap:48px;top:173px}
.add-lesson{position:absolute;right:64px;top:233px;height:40px;padding:0 24px;box-shadow:0 1px 6px rgba(0,0,0,.15);color:var(--orange);font-size:11px;font-weight:700;display:flex;align-items:center;gap:10px}
.lesson-card{position:absolute;left:65px;width:716px;height:113px;background:var(--white);box-shadow:0 2px 10px rgba(0,0,0,.1)}
.lesson-card .cover{left:36px;top:20px;width:76px;height:72px}
.lesson-card h3{position:absolute;left:150px;top:16px;color:var(--orange);font-size:13.5px;font-weight:500}
.lesson-card p{position:absolute;left:152px;top:39px;width:360px;font-size:11.5px;line-height:14px;color:#555}
.lesson-card .due{position:absolute;left:152px;top:79px;font-size:11px;font-weight:700;color:var(--red);display:flex;align-items:center;gap:10px}
.lesson-card .btn{position:absolute;left:533px;top:32px;height:32px;padding:0 13px;font-size:9.5px}
.lesson-card .gear{position:absolute;left:670px;top:43px}
.assess{position:absolute;left:72px;top:885px;width:709px;height:228px;background:var(--slate);color:var(--white);text-align:center;padding-top:30px}
.assess h2{font-size:26px;font-weight:500}
.assess h4{font-size:12px;font-weight:700;margin-top:10px}
.assess p{font-size:11.5px;line-height:19px;margin:16px auto 0;width:610px}
.assess .btn{margin-top:16px;height:32px;padding:0 13px;font-size:9.5px}
/* screen 3 */
.lead{position:absolute;left:0;right:0;top:92px;text-align:center;font-size:20px;font-weight:500;color:#111}
.search{position:absolute;left:162px;top:145px;width:520px;height:40px;display:flex;box-shadow:0 1px 5px rgba(0,0,0,.14)}
.search span{flex:1;padding-left:20px;line-height:40px;font-size:12px;color:#666}
.search b{width:117px;background:var(--orange);color:var(--white);font-size:13px;font-weight:500;display:flex;align-items:center;justify-content:center}
.library-tabs{left:139px;width:565px;top:262px;border-bottom:1px solid var(--line);justify-content:space-between;padding:0 4px}
.library-tabs .tab{padding:0 8px 12px;font-weight:500}
.cluster{position:absolute;width:175px;height:153px;border:1px solid var(--line);text-align:center;font-size:11.5px;font-weight:500;color:#222;line-height:16px;padding-top:25px}
.cluster .icon{width:54px;height:54px;border-radius:12px;background:var(--orange);margin:0 auto 22px}
.all-clusters{position:absolute;left:403px;top:931px;height:33px;padding:0 17px;font-size:10px}
</style>
</head>
<body>

<svg width="0" height="0" style="position:absolute">
  <defs>
    <symbol id="i-mail" viewBox="0 0 12 9"><rect width="12" height="9" rx="1" fill="#f7941d"/><path d="M0 1l6 4 6-4" stroke="#fff" stroke-width="1.2" fill="none"/></symbol>
    <symbol id="i-user" viewBox="0 0 10 11"><circle cx="5" cy="3" r="2.8" fill="#f7941d"/><path d="M0 11c0-3.5 2.3-5 5-5s5 1.5 5 5z" fill="#f7941d"/></symbol>
    <symbol id="i-gear" viewBox="0 0 20 20"><circle cx="10" cy="10" r="7" fill="none" stroke="#f7941d" stroke-width="4" stroke-dasharray="3 2.5"/><circle cx="10" cy="10" r="5" fill="none" stroke="#f7941d" stroke-width="3"/></symbol>
    <symbol id="i-bell" viewBox="0 0 18 20"><path d="M9 1c-4 0-6 3-6 7v5l-2 3h16l-2-3V8c0-4-2-7-6-7z" fill="#f7941d"/><circle cx="9" cy="18" r="2" fill="#f7941d"/></symbol>
    <symbol id="i-back" viewBox="0 0 10 16"><path d="M8 2L2 8l6 6" stroke="#222" stroke-width="2" fill="none"/></symbol>
    <symbol id="i-cal" viewBox="0 0 10 10"><rect y="1" width="10" height="9" rx="1" fill="#f7941d"/><rect x="1.5" y="4" width="7" height="4.5" fill="#fff"/></symbol>
    <symbol id="i-chev" viewBox="0 0 12 8"><path d="M1 1l5 5 5-5" stroke="#f7941d" stroke-width="2" fill="none"/></symbol>
  </defs>
</svg>

<!-- ================= Career Spotlight ================= -->
<section class="screen screen-1">
  <aside class="sidebar">
    <div class="brand"><span class="brand-mark"></span><span class="brand-name">TRAILMARK CAREERS</span></div>
    <ul class="nav">
      <li><i></i>HOME</li><li><i></i>CLASS LESSON</li><li><i></i>CAREER TOOLS</li><li><i></i>CAREER DETAILS</li><li><i></i>MY CAREER</li>
    </ul>
  </aside>
  <header class="topbar">
    <span class="mail"><svg class="ic" width="12" height="9"><use href="#i-mail"/></svg>hello@trailmark-learn.org</span>
    <span class="login"><svg class="ic" width="10" height="11"><use href="#i-user"/></svg>LOGIN</span>
    <div class="right">
      <svg class="ic" width="20" height="20"><use href="#i-gear"/></svg>
      <svg class="ic" width="18" height="20" style="margin-left:30px"><use href="#i-bell"/></svg>
      <span class="avatar" role="img" aria-label="User profile photo"></span>
      <div class="user"><b>JOHN DOE</b><span>Businessman</span></div>
    </div>
  </header>
  <main class="main">
    <h1 class="page-title">CAREER SPOTLIGHT</h1>
    <div class="spotlight">
      <div class="job-title">Plumbers, Pipefitters, &amp; Steamfitters</div>
      <div class="label">WHAT THEY DO</div>
      <p>Assemble, install, alter, and repair pipelines or pipe systems that carry water, steam, air, or oher liquids or gases. May install heating and cooling equipment and mechanical control systems, Includes sprinkler fitters.</p>
      <div class="label" style="margin-top:22px">EARNINGS</div>
      <div class="earnings">
        <div>Low End<b>$33,46</b></div>
        <div>Median<b>$56,330</b></div>
        <div>High End<b>$98,990</b></div>
      </div>
      <span class="btn btn-dark">LEARN MORE <span class="dot"></span></span>
    </div>
    <div class="media"><div class="photo" role="img" aria-label="Video still of a plumber repairing pipes under a sink"><span class="play"></span></div></div>

    <h2 class="h-section" style="left:49px;top:480px">CLASSES</h2>
    <span class="view-all">VIEW ALL <span class="btn-orange" style="width:9px;height:9px;border-radius:50%;display:block"></span></span>
    <div class="class-card" style="left:39px">
      <div class="who"><svg class="ic" width="10" height="11"><use href="#i-user"/></svg>MATH TEACHER</div>
      <div class="period">Period 1</div>
      <div class="sub">8 th Grade Math / Pre - Algebra</div>
      <span class="btn btn-dark">GO TO CLASS <span class="dot"></span></span>
      <div class="cover" role="img" aria-label="Course book cover: 8th Grade Math / Pre-Algebra"></div>
    </div>
    <div class="class-card" style="left:447px">
      <div class="who"><svg class="ic" width="10" height="11"><use href="#i-user"/></svg>MATH TEACHER</div>
      <div class="period">Period 1</div>
      <div class="sub">8 th Grade Math / Pre - Algebra</div>
      <span class="btn btn-dark">GO TO CLASS <span class="dot"></span></span>
      <div class="cover" role="img" aria-label="Course book cover: 8th Grade Math / Pre-Algebra"></div>
    </div>

    <h2 class="h-section" style="left:49px;top:768px">UPCOMING LESSONS</h2>
    <div class="lessons-intro">Sed ut perspiciatis unde omnis iste natus error sit voluptatem accusantium doloremque laudantium</div>
    <table class="table">
      <tr><th>CLASS</th><th>LESSON</th><th>DUE</th></tr>
      <tr><td>Period 1</td><td>1.1 - Translation</td><td class="due">October 15 th at 11.59 PM</td></tr>
      <tr><td>Period 1</td><td>1.1 - Translation</td><td class="due">October 15 th at 11.59 PM</td></tr>
      <tr><td>Period 1</td><td>1.1 - Translation</td><td class="due">October 15 th at 11.59 PM</td></tr>
      <tr><td>Period 1</td><td>1.1 - Translation</td><td class="due">October 15 th at 11.59 PM</td></tr>
    </table>
  </main>
</section>

<!-- ================= Browse All Courses ================= -->
<section class="screen screen-2">
  <aside class="sidebar">
    <div class="brand"><span class="brand-mark"></span><span class="brand-name">TRAILMARK CAREERS</span></div>
    <ul class="nav">
      <li><i></i>HOME</li><li><i></i>CLASS LESSON</li><li><i></i>CAREER TOOLS</li><li><i></i>CAREER DETAILS</li><li><i></i>MY CAREER</li>
    </ul>
  </aside>
  <header class="topbar">
    <span class="mail"><svg class="ic" width="12" height="9"><use href="#i-mail"/></svg>hello@trailmark-learn.org</span>
    <span class="login"><svg class="ic" width="10" height="11"><use href="#i-user"/></svg>LOGIN</span>
    <div class="right">
      <svg class="ic" width="20" height="20"><use href="#i-gear"/></svg>
      <svg class="ic" width="18" height="20" style="margin-left:30px"><use href="#i-bell"/></svg>
      <span class="avatar" role="img" aria-label="User profile photo"></span>
      <div class="user"><b>JOHN DOE</b><span>Businessman</span></div>
    </div>
  </header>
  <main class="main">
    <svg class="back" width="10" height="16"><use href="#i-back"/></svg>
    <h1 class="page-title">BROWSE ALL COURSES</h1>
    <div class="teacher-row">
      <span class="who"><svg class="ic" width="10" height="11"><use href="#i-user"/></svg>MATH TEACHER</span>
      <span class="period">Period 1</span>
      <span class="sub">8 th Grade Math / Pre - Algebra</span>
      <span class="btn btn-orange">CLASS ROSTER <span class="dot"></span></span>
      <span class="btn btn-dark">CLASS SETTINGS <span class="dot"></span></span>
    </div>
    <div class="tabs lesson-tabs">
      <span class="tab active">LESSONS <span style="width:10px;height:10px;border-radius:50%;background:var(--orange);display:block"></span></span>
      <span class="tab">SCORES <span style="width:10px;height:10px;border-radius:50%;background:#222;display:block"></span></span>
    </div>
    <h2 class="h-section" style="left:64px;top:237px;font-size:24px;display:flex;align-items:center;gap:12px">UPCOMING LESSON <svg class="ic" width="12" height="8"><use href="#i-chev"/></svg></h2>
    <span class="add-lesson">ADD LESSON <b>+</b></span>

    <article class="lesson-card" style="top:297px">
      <div class="cover" role="img" aria-label="Lesson book cover"></div>
      <h3>1.1 - TRANSLATIONS</h3>
      <p>Sed ut perspiciatis unde omnis iste natus error sit voluptatem accusantium doloremque laudantium,</p>
      <span class="due"><svg class="ic" width="10" height="10"><use href="#i-cal"/></svg>DUE : 10/15 AT 11.59 PM</span>
      <span class="btn btn-orange">BEGIN LESSON <span class="dot"></span></span>
      <svg class="ic gear" width="12" height="12"><use href="#i-gear"/></svg>
    </article>
    <article class="lesson-card" style="top:443px">
      <div class="cover" role="img" aria-label="Lesson book cover"></div>
      <h3>1.1 - TRANSLATIONS</h3>
      <p>Sed ut perspiciatis unde omnis iste natus error sit voluptatem accusantium doloremque laudantium,</p>
      <span class="due"><svg class="ic" width="10" height="10"><use href="#i-cal"/></svg>DUE : 10/15 AT 11.59 PM</span>
      <span class="btn btn-orange">BEGIN LESSON <span class="dot"></span></span>
      <svg class="ic gear" width="12" height="12"><use href="#i-gear"/></svg>
    </article>
    <article class="lesson-card" style="top:589px">
      <div class="cover" role="img" aria-label="Lesson book cover"></div>
      <h3>1.1 - TRANSLATIONS</h3>
      <p>Sed ut perspiciatis unde omnis iste natus error sit voluptatem accusantium doloremque laudantium,</p>
      <span class="due"><svg class="ic" width="10" height="10"><use href="#i-cal"/></svg>DUE : 10/15 AT 11.59 PM</span>
      <span class="btn btn-orange">BEGIN LESSON <span class="dot"></span></span>
      <svg class="ic gear" width="12" height="12"><use href="#i-gear"/></svg>
    </article>
    <article class="lesson-card" style="top:735px">
      <div class="cover" role="img" aria-label="Lesson book cover"></div>
      <h3>1.1 - TRANSLATIONS</h3>
      <p>Sed ut perspiciatis unde omnis iste natus error sit voluptatem accusantium doloremque laudantium,</p>
      <span class="due"><svg class="ic" width="10" height="10"><use href="#i-cal"/></svg>DUE : 10/15 AT 11.59 PM</span>
      <span class="btn btn-orange">BEGIN LESSON <span class="dot"></span></span>
      <svg class="ic gear" width="12" height="12"><use href="#i-gear"/></svg>
    </article>

    <div class="assess">
      <h2>TMC ASSESSMENTS</h2>
      <h4>LOOKING FOR YOUR UPCOMING TMC ASSESSMENT</h4>
      <p>Sed ut perspiciatis unde omnis iste natus error sit voluptatem accusantium doloremque laudantium, totam rem aperiam, eaque ipsa quae ab illo inventore veritatis et quasi architecto beatae vitae dicta sunt explicabo</p>
      <span class="btn btn-orange">GO THERE NOW <span class="dot"></span></span>
    </div>
  </main>
</section>

<!-- ================= Career Library ================= -->
<section class="screen screen-3">
  <aside class="sidebar">
    <div class="brand"><span class="brand-mark"></span><span class="brand-name">TRAILMARK CAREERS</span></div>
    <ul class="nav">
      <li><i></i>HOME</li><li><i></i>CLASS LESSON</li><li><i></i>CAREER TOOLS</li><li><i></i>CAREER DETAILS</li><li><i></i>MY CAREER</li>
    </ul>
  </aside>
  <header class="topbar">
    <span class="mail"><svg class="ic" width="12" height="9"><use href="#i-mail"/></svg>hello@trailmark-learn.org</span>
    <span class="login"><svg class="ic" width="10" height="11"><use href="#i-user"/></svg>LOGIN</span>
    <div class="right">
      <svg class="ic" width="20" height="20"><use href="#i-gear"/></svg>
      <svg class="ic" width="18" height="20" style="margin-left:30px"><use href="#i-bell"/></svg>
      <span class="avatar" role="img" aria-label="User profile photo"></span>
      <div class="user"><b>JOHN DOE</b><span>Businessman</span></div>
    </div>
  </header>
  <main class="main">
    <svg class="back" width="10" height="16"><use href="#i-back"/></svg>
    <h1 class="page-title">CAREER LIBRARY</h1>
    <div class="lead">Explore Career to find Jobs that match your Interest and skill yet</div>
    <div class="search"><span>Search All Careers</span><b>SEARCH</b></div>
    <div class="tabs library-tabs">
      <span class="tab active">CAREER CLUSTER</span>
      <span class="tab">VALUES &amp; INTEREST</span>
      <span class="tab">EDUCATION ZONE</span>
    </div>

    <div class="cluster" style="left:55px;top:343px"><div class="icon" role="img" aria-label="Agriculture cluster icon"></div>Lorem ipsum dolor sit amet<br>consectetur</div>
    <div class="cluster" style="left:242px;top:343px"><div class="icon" role="img" aria-label="Manufacturing cluster icon"></div>Lorem ipsum dolor sit amet<br>consectetur</div>
    <div class="cluster" style="left:427px;top:343px"><div class="icon" role="img" aria-label="Arts cluster icon"></div>Lorem ipsum dolor sit amet<br>consectetur</div>
    <div class="cluster" style="left:614px;top:343px"><div class="icon" role="img" aria-label="Human services cluster icon"></div>Lorem ipsum dolor sit amet<br>consectetur</div>

    <div class="cluster" style="left:55px;top:509px"><div class="icon" role="img" aria-label="Education cluster icon"></div>Lorem ipsum dolor sit amet<br>consectetur</div>
    <div class="cluster" style="left:242px;top:509px"><div class="icon" role="img" aria-label="Finance cluster icon"></div>Lorem ipsum dolor sit amet<br>consectetur</div>
    <div class="cluster" style="left:427px;top:509px"><div class="icon" role="img" aria-label="Government cluster icon"></div>Lorem ipsum dolor sit amet<br>consectetur</div>
    <div class="cluster" style="left:614px;top:509px"><div class="icon" role="img" aria-label="Health science cluster icon"></div>Lorem ipsum dolor sit amet<br>consectetur</div>

    <div class="cluster" style="left:55px;top:676px"><div class="icon" role="img" aria-label="Hospitality cluster icon"></div>Lorem ipsum dolor sit amet<br>consectetur</div>
    <div class="cluster" style="left:242px;top:676px"><div class="icon" role="img" aria-label="Community services cluster icon"></div>Lorem ipsum dolor sit amet<br>consectetur</div>
    <div class="cluster" style="left:427px;top:676px"><div class="icon" role="img" aria-label="Technology cluster icon"></div>Lorem ipsum dolor sit amet<br>consectetur</div>
    <div class="cluster" style="left:614px;top:676px"><div class="icon" role="img" aria-label="Law and public safety cluster icon"></div>Lorem ipsum dolor sit amet<br>consectetur</div>

    <span class="btn btn-orange all-clusters">ALL CAREER CLUSTER <span class="dot"></span></span>
  </main>
</section>

</body>
</html>
```